Corporate website design needed

We need a Contemporary Industrial/Tech/Logistics Website design to match our logistic client's business. Our client consults and build logistics solutions that they manage but they are not a typical 3PL (3rd party logistics company) which is primarily engaged in moving boxes.
PSD file only for now, home and default templates.
COMPANY CHARACTER
DESIGN LOOK AND FEEL
• The design should also be modern and visually well organized — employing a combination of visual devices and info graphics. Keep it light and not too heavy but strong/ professional. And unique.
• The design should go beyond the typical industrial pick and pack 3PL representing [Logistics Company] as a High Tech/IT logistics company.
Some examples although these are not right for this client because they have much more content and present themselves more as a 3pl.
http://www.vobrelink-hub.example/ (More right then wrong - Like this but simplified)
http://www.durmaxfreight.example (Ugly)
http://www.tpwallerton.example (More right then wrong but different focus)
http://www.pelhamrye.example/ Too 3PL trucking… We want a bit ore high level approach
The difference, the design should be a fusion in core concepts that culminate in a design which implies the following attributes. Tech (Big data / analytics / software), Consultancy (Solutions, SME, Leader), 3PL Industry vertical solutions.
NOTE: The visualization of “tech” is not “1” and “0”, but more “software and analytics” Perhaps more like www.navimetra.example.
• They need to be seen as a solutions provider in Logistics and as in Subject matter experts
TONE
The tone needs to exude professionalism, expertise, though leadership along with technical and executional excellence.
Experienced
Knowledgeable
Confident
Determined
Straightforward
WEBSITE OBJECTIVES
• Focus C-Suite executives and logistics managers’ attention on [Logistics Company]s commanding knowledge and expertise, and unique approach to supply chain solutions producing more RFP wins
• Create an easy to scan design which decreases the reliance on text through featured text, summaries, and smaller “chunked” size bits of information.
• Convey [Logistics Company] as high-tech 3PL solutions developer and services provider with a ‘high-touch’ consultative approach.
• Showcase [Logistics Company]’s value propositions. (See Slider Content)
• Showcase [Logistics Company]’s expertise in logistical analytics.
• Gain recognition as an industry leader in evolutionary new space (supply chain 2.0)
WEBSITE STRATEGY
• Reduce reliance on text (at least within initial entry points for each section)
• Typography: Watch text line lengths and readability, bolder fonts. NO SERIFS
• Generally, create a click-through format so that users who want more details can find it, and those who don’t can get a snapshot without clicking through.
• Increase visual content through info graphics and some dynamic content, photography
• Better utilize the space on each page (e.g., add visual interest, photography and iconography where appropriate to break up copy blocks and maintain readable line lengths).
COLOR SCHEME
• Create a more engaging color scheme (the logo will remain the same under all circumstances).
• Red / grayscale may work…. Not too dark or heavy. Not too much red. Ex. quiltora.example
• Also try blues and greys. They seem to like that. Open to suggestions but don’t get to crazy. Red is in their logo but too much may be a problem.
PHOTOGRAPHY
Yes. And I will upload some.
If you pick photography please be sure to note Which stock house used and the image number!
CONTENT
The content will be presented in a more hierarchical format — with lead-ins, paragraph and section headers and navigational cues to expand lengthier content allowing the visitor to more easily scan the website. No case studies, No Social media, News while on the home page should not be over emphasized. They don't post a lot so it gets dated quickly ...
I will be uploading a wire frame and other elements.
NOTE: I uploaded my EXAMPLE mock up which is close but not close enough.
I am not a great designer. So I am looking for an alternative that exceed my design ability! These examples show the basic layout but I really want some varied alternatives.
The colors are inconsistent and type not quite right. The grey bar at top is not right and should probably go away.
Please pull the basic elements in the example together into a great design.
If you have questions please contact me.
i will upload some photography tomorrow that may be of use.
Thanks!
Updates
Hi All,
We are still evaluating the submitted designs. Sorry for the delay.
Target Market(s)
This website is primarily a validation website. Few new customers will search and find them as such...
The site should be Focused on C-Suite executives and logistics managers’ attention on [Logistics Company]s commanding knowledge and expertise, and unique approach to supply chain solutions producing more RFP wins
Industry/Entity Type
Business
Font styles to use
Requirements
Must have
- Slide show, Clearly explain who they are and what they do.
Create an easy to scan design which decreases the reliance on text through featured text, summaries, and smaller “chunked” size bits of information.
Convey [Logistics Company] as high-tech 3PL solutions developer and services
provider with a ‘high-touch’ consultative approach.
Should not have
- No Ads space
No Social media
Not too cluttered. Keep it clean.

```html
<!DOCTYPE html>
<html lang="en">
<head>
<meta charset="utf-8">
<title>Corvane Logistics</title>
<link href="https://fonts.googleapis.com/css2?family=Open+Sans:wght@400;600;700&display=swap" rel="stylesheet">
<style>
:root{
  --red:#c8311f;
  --red-dark:#a3200f;
  --ink:#222;
  --grey:#555;
  --light:#eef0f2;
  --black:#111;
  --white:#fff;
  --blue-a:#dcecf7;
  --blue-b:#5fa4d6;
}
*{margin:0;padding:0;box-sizing:border-box}
html,body{width:686px;height:1200px;overflow:hidden}
body{font-family:"Open Sans",Arial,sans-serif;color:var(--ink);background:linear-gradient(#fff 0,#f6f7f8 600px,#e9ebee 890px);position:relative}
a{color:inherit;text-decoration:none}

.utility{position:absolute;top:6px;right:96px;font-size:9px;color:var(--red)}
.utility .sales{font-weight:700;margin-left:10px}
.brand{position:absolute;top:32px;left:92px;display:flex;align-items:center;gap:7px}
.brand-dot{width:26px;height:26px;border-radius:50%;background:var(--red)}
.brand-name{font-size:11px;font-weight:700;letter-spacing:2px;color:var(--red);text-transform:uppercase}
.main-nav{position:absolute;top:30px;right:96px;background:var(--black);color:var(--white);font-size:9.5px;font-weight:600;padding:6px 12px;display:flex;gap:10px}
.main-nav span.sep{color:#777}

.hero{position:absolute;left:92px;top:68px;width:500px;height:238px;box-shadow:0 2px 6px rgba(0,0,0,.25)}
.hero-media{width:100%;height:196px;background:radial-gradient(circle at 70% 45%,#f4f9fd 0,var(--blue-a) 30%,var(--blue-b) 100%)}
.hero-caption{height:42px;background:var(--red);color:var(--white);font-size:11.5px;display:flex;align-items:center;justify-content:space-between;padding:0 14px 0 18px}
.dots{display:flex;gap:4px}
.dots i{width:7px;height:7px;border-radius:50%;background:#f3b3aa}
.dots i.on{background:var(--white)}

.section-title{position:absolute;left:0;width:686px;text-align:center;font-size:17px;font-weight:400;color:#333;letter-spacing:.5px}
.offer-title{top:320px}
.offers{position:absolute;top:358px;left:100px;width:486px;display:flex;justify-content:space-between}
.offer{width:86px;text-align:center;font-size:7px;color:#333;line-height:1.3}
.offer-icon{width:42px;height:46px;margin:0 auto 8px;border-radius:4px;background:linear-gradient(135deg,#d9c9a8,#a88a5c)}
.offer-icon.cart{background:linear-gradient(135deg,#f2d0cc,#c8311f)}
.offer-icon.chart{background:linear-gradient(135deg,#f6d27a,#3a7bc8)}
.offer-icon.box{background:linear-gradient(135deg,#f1e3b4,#c9a44c)}
.offer-icon.tools{background:linear-gradient(135deg,#f0f0f0,#9a9a9a)}

.values{position:absolute;top:474px;left:0;width:686px;text-align:center}
.value h3{font-size:9.5px;font-weight:700;color:var(--red);letter-spacing:.3px}
.value p{font-size:8.5px;color:var(--grey);margin:2px 0 13px}

.video-title{top:606px}
.video{position:absolute;left:167px;top:660px;width:393px;height:222px;box-shadow:0 2px 6px rgba(0,0,0,.25)}
.video-media{width:100%;height:100%;background:linear-gradient(160deg,#e7ecf0,#9aa9b6 60%,#54606b)}
.play{position:absolute;left:50%;top:44%;transform:translate(-50%,-50%)}
.controls{position:absolute;left:10px;right:10px;bottom:10px;height:22px;background:rgba(20,24,28,.85);border-radius:3px;display:flex;align-items:center;padding:0 8px;gap:8px}
.track{flex:1;height:5px;background:#5a6470;border-radius:3px;position:relative}
.track b{position:absolute;left:0;top:0;height:5px;width:28%;background:#4fa3e0;border-radius:3px}
.ctrl{width:9px;height:9px;background:#cfd6dc;border-radius:1px}

.news{position:absolute;top:898px;left:0;width:686px;height:58px;background:var(--black);color:var(--white)}
.news h2{position:absolute;left:86px;top:18px;font-size:15px;font-weight:400;letter-spacing:.5px}
.news-item{position:absolute;left:206px;top:10px;width:400px;font-size:7px;line-height:1.3}
.news-item h4{font-size:9px;font-weight:700;line-height:1.3}
.news-item p{font-size:7px;color:#ccc;line-height:1.3;margin-top:2px;white-space:nowrap;overflow:hidden}
.news-item a{display:block;font-size:7px;font-weight:700;line-height:1.3;margin-top:1px}

.site-footer{position:absolute;top:956px;left:0;width:686px;height:222px;background:var(--red);color:var(--white)}
.footer-cols{position:absolute;left:90px;top:16px;display:flex}
.footer-col{font-size:8.5px;line-height:1.6}
.footer-col h5{font-size:9px;font-weight:700;margin-bottom:2px}
.footer-col:nth-child(1){width:160px}
.footer-col:nth-child(2){width:126px}
.footer-col:nth-child(3){width:115px}
.legal{position:absolute;top:1178px;left:0;width:686px;height:22px;background:var(--red-dark);color:var(--white);font-size:8px;text-align:center;line-height:22px}
.legal .code{position:absolute;right:94px}
</style>
</head>
<body>

<header>
  <div class="utility">Company | Careers | Contact | Search <span class="sales">Sales: 866-555-0142</span></div>
  <div class="brand"><span class="brand-dot"></span><span class="brand-name">Corvane Logistics</span></div>
  <nav class="main-nav"><a>Solutions</a><span class="sep">|</span><a>Our Process</a><span class="sep">|</span><a>Industries</a></nav>
</header>

<section class="hero">
  <div class="hero-media" role="img" aria-label="Abstract blue data network of connected nodes and lines"></div>
  <div class="hero-caption">
    <span>A new way to think about supply chain transformation</span>
    <span class="dots"><i class="on"></i><i></i><i></i><i></i></span>
  </div>
</section>

<h2 class="section-title offer-title">WHAT WE OFFER</h2>
<div class="offers">
  <div class="offer"><div class="offer-icon" role="img" aria-label="Stacked boxes icon"></div>Material Management &amp; Factory Support</div>
  <div class="offer"><div class="offer-icon cart" role="img" aria-label="Shopping cart icon"></div>Retail and e-Commerce Distribution</div>
  <div class="offer"><div class="offer-icon chart" role="img" aria-label="Bar chart icon"></div>Aftermarket Support</div>
  <div class="offer"><div class="offer-icon box" role="img" aria-label="Package icon"></div>Critical Logistics</div>
  <div class="offer"><div class="offer-icon tools" role="img" aria-label="Tools icon"></div>Supply Chain Transformation Services</div>
</div>

<div class="values">
  <div class="value"><h3>A DIFFERENT INCENTIVE</h3><p>We commit our own capital and resources to align with our clients' goals</p></div>
  <div class="value"><h3>A DIFFERENT APPROACH</h3><p>Unlike consultants, we implement and operate the solutions we design</p></div>
  <div class="value"><h3>A DIFFERENT LEVEL OF COMMITMENT</h3><p>We guarantee business performance for our clients by investing in and executing the solutions we design.</p></div>
</div>

<h2 class="section-title video-title">CORPORATE PROFILE VIDEO</h2>
<div class="video">
  <div class="video-media" role="img" aria-label="Video still of a business meeting in a bright office"></div>
  <svg class="play" width="44" height="44" viewBox="0 0 44 44"><rect width="44" height="44" rx="6" fill="rgba(20,24,28,.75)"/><path d="M17 13 L31 22 L17 31 Z" fill="#fff"/></svg>
  <div class="controls">
    <svg width="9" height="9" viewBox="0 0 9 9"><path d="M1 0 L9 4.5 L1 9 Z" fill="#cfd6dc"/></svg>
    <div class="track"><b></b></div>
    <span class="ctrl"></span><span class="ctrl"></span><span class="ctrl"></span>
  </div>
</div>

<section class="news">
  <h2>RECENT NEWS</h2>
  <div class="news-item">
    <h4>Corvane Logistics Ranked #1 in Distribution Operations in the Memphis area</h4>
    <p>CARY, NC – May 16, 2013 – Corvane Logistics Inc., headquartered in Cary, North Carolina, has been recognized for its operations.</p>
    <a>Read more</a>
  </div>
</section>

<footer class="site-footer">
  <div class="footer-cols">
    <div class="footer-col"><h5>Our Process</h5>Concept of operations<br>Supplying the infrastructure<br>Analyzing the data<br>Managing complexity<br>Providing actionable strategies<br>Investing in our client's success<br>Driving business results</div>
    <div class="footer-col"><h5>Our Solutions</h5>Business Analytics<br>Geographic Coverage<br>Project Financing<br>Project Implementation<br>Technology<br>Quality</div>
    <div class="footer-col"><h5>Industries We Serve</h5>Aerospace<br>Defense<br>Industrial<br>Manufacturing<br>Media and Entertainment<br>Medical<br>Retail<br>Telecom &amp; Electronics</div>
    <div class="footer-col"><h5>Company</h5>Culture<br>Community Involvement<br>Major Metro Presence<br>News<br>Careers<br>Contact</div>
  </div>
</footer>
<div class="legal">© Corvane, Inc. 2014Privacy Policy Terms of Use <span class="code">CS</span></div>

</body>
</html>
```